Mortgage Company ready to make a statement!

We have a basic logo that I am fairly happy with ... but it could use a little bit of tweaking before we order the sign for our building. We also want some knock-your-socks-off business cards.
Problem: Inside of our Mortgage Office (Bright Fern Mortgage Group), we are going to have a coffee lounge (Sunbrew Cafe) for Realtors to use instead of the local Cuppington to meet with homebuyers. The office and coffee lounge are in an industrial building and is decorated with cozy overstuffed chairs, a hodge podge of interesting lamps and furniture, and goal is to make it as inviting as possible. However, we are a financial institution... so we need to keep it pretty clean as well.
One of my favorite marketing ideas is to cut a house key for everyone who buys a home using us with a key that matches our logo. There's only one key shape that works really well, so that needs to match the logo in order for the idea to work. I'll attach an image of the key blank.... although the way the key hole cut out looks terrible, so I was thinking of having them just do a thin outline instead.
Would like a similar, matching logo for the Sunbrew Cafe... but possibly something that would be a little less formal and would be cute on a coffee mug- nothing stuffy.
AND, we're opening a home inspection company as well, and we would like that logo and branding to match. The home inspection company is "Bright Fern Home Inspections"
We were thinking that for the home inspection company , we could use a magnifying glass shape inside of the house shape for the logo, use a keyhole shape inside of the same house for the mortgage company, and use a coffee cup inside of the house shape for Sunbrew Cafe.
Just getting stuck and need to help. I designed the attached logo myself, and that is what we are currently using. Designers at local printing companies have failed to impress us.
The mortgage industry has a lot of numbers and logos, etc that they require us to put on our business cards... so it's hard to keep them looking clean.
HELP! HELP! :)

```html
<!DOCTYPE html>
<html lang="en">
<head>
<meta charset="utf-8">
<title>Bright Fern Mortgage Group – Business Card</title>
<link rel="stylesheet" href="https://fonts.googleapis.com/css2?family=Open+Sans:wght@400;600&family=Raleway:wght@500&display=swap">
<style>
  :root {
    --brand-blue: #236487;
    --ink-blue: #1f6184;
    --paper: #ffffff;
    --backdrop: #ecebe9;
    --keyhole-light: #e9e6e2;
    --keyhole-shade: #bdb8b3;
    --badge-grey: #3b3b3b;
  }
  * { margin: 0; padding: 0; box-sizing: border-box; }
  html, body { width: 1200px; height: 1187px; overflow: hidden; }
  body {
    position: relative;
    background: var(--backdrop);
    font-family: "Open Sans", Arial, sans-serif;
  }
  .card {
    position: absolute;
    width: 565px;
    height: 351px;
    box-shadow: 0 6px 18px rgba(0,0,0,0.18);
  }
  .card-front { left: 327px; top: 193px; background: var(--brand-blue); color: #fff; }
  .card-back  { left: 556px; top: 662px; background: var(--paper); color: var(--ink-blue); }

  .wordmark {
    position: absolute;
    display: flex;
    align-items: center;
    gap: 10px;
    font-family: "Raleway", Arial, sans-serif;
    font-weight: 500;
    font-size: 23px;
    line-height: 1.15;
    letter-spacing: 0.5px;
    text-transform: uppercase;
    white-space: nowrap;
  }
  .wordmark .mark-square { width: 26px; height: 26px; flex: none; }
  .card-front .wordmark { left: 38px; top: 38px; color: #fff; }
  .card-front .wordmark .mark-square { background: #fff; }
  .card-back .wordmark { left: 218px; top: 112px; color: var(--ink-blue); }
  .card-back .wordmark .mark-square { background: var(--ink-blue); }

  .person { position: absolute; left: 38px; top: 130px; }
  .person-name { font-weight: 600; font-size: 19px; line-height: 22px; letter-spacing: 0.2px; }
  .person-role { font-size: 15px; line-height: 22px; }
  .person-license { font-size: 15px; line-height: 22px; }

  .contact-list { position: absolute; left: 38px; top: 211px; list-style: none; font-size: 15px; }
  .contact-list li { display: flex; align-items: center; gap: 6px; height: 20px; white-space: nowrap; }
  .contact-list svg { width: 11px; height: 11px; fill: #fff; flex: none; }

  .address { position: absolute; left: 38px; top: 285px; font-size: 15px; line-height: 19px; white-space: nowrap; }

  .keyhole-panel {
    position: absolute;
    background: linear-gradient(135deg, var(--keyhole-light), var(--keyhole-shade));
    border-radius: 4px;
  }
  .card-front .keyhole-panel { left: 393px; top: 107px; width: 84px; height: 173px; }
  .card-back .keyhole-panel  { left: 88px;  top: 108px; width: 82px; height: 170px; }

  .division-note {
    position: absolute;
    left: 252px; top: 188px;
    width: 240px;
    text-align: center;
    font-size: 13px;
    line-height: 18px;
  }
  .compliance-badge {
    position: absolute;
    left: 457px; top: 236px;
    width: 64px; height: 64px;
    background: var(--badge-grey);
    border-radius: 3px;
  }
</style>
</head>
<body>
  <section class="card card-front" aria-label="Business card front">
    <div class="wordmark"><span class="mark-square"></span><span>Bright Fern<br>Mortgage Group</span></div>

    <div class="person">
      <p class="person-name">DANIEL REYES</p>
      <p class="person-role">Managing Director</p>
      <p class="person-license">NMLS# 48213975</p>
    </div>

    <ul class="contact-list">
      <li>
        <svg viewBox="0 0 12 12"><path d="M2.5 0.8 L4.3 0.5 L5.3 3.1 L4 4.1 C4.7 5.7 6 7 7.7 7.8 L8.7 6.5 L11.4 7.5 L11.1 9.4 C10.9 10.6 9.9 11.3 8.8 11.1 C4.7 10.4 1.5 7.2 0.8 3.1 C0.6 2 1.3 1 2.5 0.8 Z"/></svg>
        <span>(044)987654321</span>
      </li>
      <li>
        <svg viewBox="0 0 12 12"><path d="M0.5 2 H11.5 V10 H0.5 Z M1.5 3 L6 6.5 L10.5 3 V2.9 H1.5 Z" fill-rule="evenodd"/></svg>
        <span>hello@brightfernmg.com</span>
      </li>
      <li>
        <svg viewBox="0 0 12 12"><circle cx="6" cy="6" r="5.5"/><path d="M3 4.5 C4.5 4 5 5.5 4.2 6.5 C3.6 7.3 4.5 8.7 5.3 9.5 M7.5 2 C7 3.2 8.3 3.8 9.4 4.3" stroke="var(--brand-blue)" stroke-width="1.2" fill="none"/></svg>
        <span>www.brightfernmg.com</span>
      </li>
    </ul>

    <p class="address">No. 18, Millbrook Avenue,<br>Riverton, OR 97402</p>

    <div class="keyhole-panel" role="img" aria-label="Embossed decorative panel"></div>
  </section>

  <section class="card card-back" aria-label="Business card back">
    <div class="keyhole-panel" role="img" aria-label="Embossed decorative panel"></div>
    <div class="wordmark"><span class="mark-square"></span><span>Bright Fern<br>Mortgage Group</span></div>
    <p class="division-note">Bright Fern Mortgage Group is a division of Harlow Lending</p>
    <div class="compliance-badge" aria-label="Compliance badge"></div>
  </section>
</body>
</html>
```